Qvx Brightforge Website

All the descriptions are available in the attached file. The designer has to structure the website and find the right images and icons. The website should look modern and avoid using images of real humans rather use animated images. Please note that the design should include home page, all the 4 services page , the contact us would be at the bottom of home page.

```html
<!DOCTYPE html>
<html lang="en">
<head>
<meta charset="utf-8">
<title>Qvx Brightforge</title>
<link href="https://fonts.googleapis.com/css2?family=Orbitron:wght@600;700;800&family=Roboto:wght@400;500;700&display=swap" rel="stylesheet">
<style>
:root{
  --blue:#0b6fe0;
  --blue-deep:#075bc9;
  --blue-band:#1478ea;
  --ink:#121212;
  --text:#6d6d6d;
  --pale:#f2f6fc;
  --white:#ffffff;
  --black:#000000;
}
*{margin:0;padding:0;box-sizing:border-box}
html,body{width:1200px;height:4815px;overflow:hidden}
body{position:relative;background:var(--white);font-family:'Roboto',sans-serif;color:var(--text)}
.abs{position:absolute}
.display{font-family:'Orbitron',sans-serif;font-weight:700;color:var(--ink);letter-spacing:1px}
.accent{color:var(--blue)}
.btn{position:absolute;display:flex;align-items:center;justify-content:center;border-radius:30px;background:var(--blue);color:var(--white);font-weight:700;font-size:13px}
.art{position:absolute;border-radius:30px}
.brand{font-family:'Orbitron',sans-serif;font-weight:800;color:var(--blue);display:flex;align-items:center;gap:10px}
.brand .dot{width:18px;height:18px;border-radius:50%;background:var(--blue)}
.hero-band{position:absolute;left:0;top:0}
.nav{position:absolute;top:88px;left:0;width:1200px;height:20px}
.nav a{position:absolute;color:var(--white);font-size:14px;text-decoration:none}
.hero-title{position:absolute;left:108px;top:210px;font-size:47px;line-height:63px}
.hero-copy{position:absolute;left:108px;top:482px;width:370px;font-size:14px;line-height:29px}
.section-title{position:absolute;left:0;width:1200px;text-align:center;font-size:40px}
.section-intro{position:absolute;left:180px;width:840px;text-align:center;font-size:15px;line-height:29px}
.svc-icon{position:absolute;width:72px;height:72px;border-radius:50%;background:var(--white);box-shadow:0 6px 18px rgba(20,80,160,.14);display:flex;align-items:center;justify-content:center}
.svc-title{position:absolute;font-size:27px;white-space:nowrap}
.svc-copy{position:absolute;width:420px;font-size:13px;line-height:29px}
.contact{position:absolute;left:0;top:3278px;width:1200px;height:565px;background:linear-gradient(180deg,var(--blue-band),var(--blue-deep))}
.contact .section-title{color:var(--white);top:108px}
.c-item{position:absolute;left:112px;display:flex;gap:14px;color:var(--white)}
.c-ring{width:48px;height:48px;border-radius:50%;border:2px solid var(--white);display:flex;align-items:center;justify-content:center;flex:none}
.c-item h4{font-size:16px;font-weight:500;margin-top:2px}
.c-item p{font-size:12.5px;line-height:24px}
.field{position:absolute;background:var(--white);font-size:12.5px;color:#8a8a8a;padding:18px 22px}
.submit{position:absolute;border:1.5px solid var(--white);color:var(--white);font-weight:700;font-size:16px;display:flex;align-items:center;justify-content:center}
.about-copy{position:absolute;left:645px;top:4034px;width:442px;font-size:13px;line-height:29.5px}
.footer{position:absolute;left:0;top:4424px;width:1200px;height:391px;background:var(--black);color:var(--white)}
.footer a{position:absolute;top:208px;color:var(--white);font-size:14px;text-decoration:none}
.social{position:absolute;top:258px;width:40px;height:40px;border-radius:50%;background:var(--blue);display:flex;align-items:center;justify-content:center}
.copyright{position:absolute;top:332px;width:1200px;text-align:center;font-size:14px}
</style>
</head>
<body>

<svg class="hero-band" width="1200" height="760" viewBox="0 0 1200 760" aria-hidden="true">
  <defs>
    <linearGradient id="band" x1="0" y1="0" x2="1" y2="1">
      <stop offset="0" stop-color="#0f6ff0"/>
      <stop offset="1" stop-color="#1a86f5"/>
    </linearGradient>
  </defs>
  <path d="M495 0 H1200 V470 C1120 430 1060 410 1000 400 L660 330 Q520 140 495 0 Z" fill="url(#band)"/>
</svg>

<svg class="abs" style="left:0;top:1010px" width="1200" height="2268" viewBox="0 0 1200 2268" aria-hidden="true">
  <path d="M0 0 L1200 500 V2268 H0 Z" fill="var(--pale)"/>
  <path d="M0 900 L1200 0 V2268 H0 Z" fill="var(--pale)" opacity=".6"/>
</svg>

<header>
  <div class="brand abs" style="left:108px;top:44px;font-size:22px"><span class="dot"></span>Qvx Brightforge</div>
  <nav class="nav">
    <a style="left:547px">Home</a>
    <a style="left:659px">Services</a>
    <a style="left:786px">Products</a>
    <a style="left:917px">Blog</a>
    <a style="left:1017px">Contact Us</a>
  </nav>
  <div class="btn" style="left:935px;top:22px;width:153px;height:47px;background:var(--white);color:var(--blue)">Get Started Now</div>
</header>

<section class="hero">
  <h1 class="hero-title display">ADVANCING<br>INNOVATION<br>THROUGH<br><span class="accent">IT CONSULTING</span></h1>
  <p class="hero-copy">Empower your digital journey with our advanced IT solutions. From data to web and mobile apps, we've got you covered.</p>
  <div class="btn" style="left:108px;top:594px;width:155px;height:44px">Get Started Now</div>
  <div class="art" role="img" aria-label="Isometric illustration of two consultants on a colourful data dashboard platform" style="left:595px;top:160px;width:508px;height:560px;background:radial-gradient(circle at 50% 55%,#f4f0ff 0,#dfe9ff 45%,rgba(255,255,255,0) 72%)"></div>
</section>

<section class="services">
  <h2 class="section-title display" style="top:852px">OUR <span class="accent">SERVICES</span></h2>
  <p class="section-intro" style="top:924px">Our consultants boasts a wealth of experience across various technologies and industries, possessing both commercial insight and technical expertise. This enables us to provide tailor-made, innovative solutions that cater to your specific needs and objectives.</p>

  <div class="art" role="img" aria-label="Isometric illustration of two people presenting charts on a large monitor" style="left:178px;top:1075px;width:364px;height:468px;background:linear-gradient(160deg,#e8eefc,#cfdcfa 60%,#f7f9ff)"></div>
  <div class="svc-icon" style="left:611px;top:1145px"><svg width="30" height="26" viewBox="0 0 30 26"><g fill="var(--blue)"><rect x="2" y="14" width="4" height="10"/><rect x="9" y="10" width="4" height="14"/><rect x="16" y="12" width="4" height="12"/><rect x="23" y="6" width="4" height="18"/></g><path d="M2 10 L10 4 L17 7 L27 1" stroke="var(--blue)" stroke-width="2" fill="none"/></svg></div>
  <h3 class="svc-title display" style="left:611px;top:1228px">DATA ANALYTICS</h3>
  <p class="svc-copy" style="left:611px;top:1278px">At Qvx Brightforge, our proficiency consists of linking your leadership team's objectives with the relevant data that holds significance. We recognize the importance of not only delivering precise and dependable data but also presenting</p>
  <div class="btn" style="left:611px;top:1417px;width:109px;height:38px;font-size:12px">Read More</div>

  <div class="svc-icon" style="left:174px;top:1682px"><svg width="28" height="28" viewBox="0 0 28 28"><g fill="none" stroke="var(--blue)" stroke-width="2.2" stroke-linejoin="round"><path d="M14 3 L25 9 L14 15 L3 9 Z" fill="var(--blue)"/><path d="M3 14 L14 20 L25 14"/><path d="M3 19 L14 25 L25 19"/></g></svg></div>
  <h3 class="svc-title display" style="left:174px;top:1768px">WEB DEVELOPMENT</h3>
  <p class="svc-copy" style="left:174px;top:1818px">At Qvx Brightforge, we are a trailblazing web development company committed to delivering cutting-edge digital solutions that empower businesses to excel in the ever-evolving online landscape. Our team of seasoned professionals combines</p>
  <div class="btn" style="left:174px;top:1956px;width:109px;height:38px;font-size:12px">Read More</div>
  <div class="art" role="img" aria-label="Isometric illustration of a person with a magnifying glass over server blocks and charts" style="left:645px;top:1561px;width:440px;height:552px;background:linear-gradient(170deg,#eef1fb,#d6d9f7 55%,#bdb9f0)"></div>

  <div class="art" role="img" aria-label="Isometric illustration of two people designing a large mobile app screen" style="left:127px;top:2165px;width:468px;height:400px;background:linear-gradient(160deg,#e4f3ff,#bfe3fb 55%,#e9f6ff)"></div>
  <div class="svc-icon" style="left:611px;top:2201px"><svg width="22" height="30" viewBox="0 0 22 30"><rect x="3" y="2" width="14" height="25" rx="3" fill="none" stroke="var(--blue)" stroke-width="2.2"/><circle cx="10" cy="22" r="1.6" fill="var(--blue)"/><circle cx="16" cy="14" r="4.5" fill="var(--blue)"/></svg></div>
  <h3 class="svc-title display" style="left:611px;top:2286px">MOBILE APP DEVELOPMENT</h3>
  <p class="svc-copy" style="left:611px;top:2338px">At Qvx Brightforge, we are a pioneering mobile app development company dedicated to crafting exceptional digital experiences that captivate and engage users across various platforms. Our team of expert developers and designers combines passion,</p>
  <div class="btn" style="left:611px;top:2476px;width:109px;height:38px;font-size:12px">Read More</div>

  <div class="svc-icon" style="left:174px;top:2740px"><svg width="26" height="26" viewBox="0 0 26 26"><path d="M24 2 C16 2 10 7 7 14 L12 19 C19 16 24 10 24 2 Z" fill="var(--blue)"/><path d="M7 14 L3 14 L7 9 L11 9 M12 19 L12 23 L17 19 L17 15" fill="var(--blue)"/><path d="M6 19 L2 24" stroke="var(--blue)" stroke-width="2"/></svg></div>
  <h3 class="svc-title display" style="left:174px;top:2826px">START-UP TECH PARTNER</h3>
  <p class="svc-copy" style="left:174px;top:2877px">At Qvx Brightforge, we are committed to supporting early-stage start-ups on their journey to success by providing comprehensive technical partner services. Our team of industry veterans collaborates with entrepreneurs</p>
  <div class="btn" style="left:174px;top:3014px;width:109px;height:38px;font-size:12px">Read More</div>
  <div class="art" role="img" aria-label="Isometric illustration of three people working on laptops atop a large pie chart" style="left:654px;top:2665px;width:393px;height:495px;background:linear-gradient(160deg,#f6e9fb,#7ff0dc 45%,#5a3fd6)"></div>
</section>

<section class="contact">
  <h2 class="section-title display">GET IN TOUCH WITH US</h2>
  <div class="c-item" style="top:205px">
    <div class="c-ring"><svg width="16" height="20" viewBox="0 0 16 20"><path d="M8 1 C4 1 1 4 1 8 C1 13 8 19 8 19 C8 19 15 13 15 8 C15 4 12 1 8 1 Z" fill="var(--white)"/><circle cx="8" cy="8" r="2.6" fill="var(--blue)"/></svg></div>
    <div><h4>HEAD OFFICE</h4><p>&nbsp;Suite 12/40 Harbour Lane,<br>Eastmere WA 6190</p></div>
  </div>
  <div class="c-item" style="top:318px">
    <div class="c-ring"><svg width="18" height="18" viewBox="0 0 18 18"><path d="M4 1 L7 5 L5 7 C6 10 8 12 11 13 L13 11 L17 14 L15 17 C8 17 1 10 1 3 Z" fill="var(--white)"/></svg></div>
    <div><h4>PHONE</h4><p>+61 (08) 5550 1234</p></div>
  </div>
  <div class="c-item" style="top:406px">
    <div class="c-ring"><svg width="18" height="14" viewBox="0 0 18 14"><rect x="1" y="1" width="16" height="12" rx="1.5" fill="var(--white)"/><path d="M1.5 2 L9 8 L16.5 2" stroke="var(--blue)" stroke-width="1.5" fill="none"/></svg></div>
    <div><h4>EMAIL</h4><p>dev@qvxbrightforge.example</p></div>
  </div>
  <div class="field" style="left:434px;top:205px;width:318px;height:53px">Name</div>
  <div class="field" style="left:434px;top:273px;width:318px;height:53px">Phone</div>
  <div class="field" style="left:434px;top:340px;width:318px;height:53px">Email</div>
  <div class="submit" style="left:434px;top:410px;width:318px;height:52px">Submit</div>
  <div class="field" style="left:772px;top:205px;width:318px;height:257px">Type your message</div>
</section>

<section class="about">
  <div class="art" role="img" aria-label="Isometric illustration of a person adjusting settings gears beside web page panels and folders" style="left:127px;top:3893px;width:468px;height:502px;background:linear-gradient(160deg,#eef0fa,#d9dcf3 55%,#f5f6fc)"></div>
  <h2 class="display abs" style="left:645px;top:3972px;font-size:27px">ABOUT US</h2>
  <p class="about-copy">We are a forward-thinking IT consulting firm specializing in providing cutting-edge data analytics, web application development, and mobile app development services. Our passion for innovation and technology drives us to deliver tailor-made solutions that empower businesses to thrive in the digital landscape. We take pride in our ability to collaborate with early-stage startups as their technology partner, helping them navigate the challenges of launching and scaling their ventures. Our team of experienced professionals works closely with clients,</p>
  <div class="btn" style="left:645px;top:4279px;width:109px;height:38px;font-size:12px">Read More</div>
</section>

<footer class="footer">
  <div class="brand abs" style="left:0;width:1200px;justify-content:center;top:78px;font-size:30px"><span class="dot"></span>Qvx Brightforge</div>
  <a style="left:330px">Home</a>
  <a style="left:441px">Services</a>
  <a style="left:568px">Products</a>
  <a style="left:697px">Blog</a>
  <a style="left:800px">Contact Us</a>
  <span class="social" style="left:503px"><svg width="16" height="16" viewBox="0 0 16 16"><circle cx="8" cy="8" r="6.5" fill="none" stroke="var(--white)" stroke-width="1.5"/><path d="M1.5 8 H14.5 M8 1.5 C5 5 5 11 8 14.5 C11 11 11 5 8 1.5" fill="none" stroke="var(--white)" stroke-width="1.3"/></svg></span>
  <span class="social" style="left:554px"><svg width="16" height="16" viewBox="0 0 16 16"><path d="M2 3 H14 V11 H7 L4 14 V11 H2 Z" fill="var(--white)"/></svg></span>
  <span class="social" style="left:606px"><svg width="16" height="16" viewBox="0 0 16 16"><g fill="var(--white)"><circle cx="12" cy="3.5" r="2.2"/><circle cx="4" cy="8" r="2.2"/><circle cx="12" cy="12.5" r="2.2"/></g><path d="M12 3.5 L4 8 L12 12.5" fill="none" stroke="var(--white)" stroke-width="1.4"/></svg></span>
  <span class="social" style="left:657px"><svg width="16" height="16" viewBox="0 0 16 16"><path d="M8 1.5 L10 6 L14.5 6.3 L11 9.3 L12.2 14 L8 11.4 L3.8 14 L5 9.3 L1.5 6.3 L6 6 Z" fill="var(--white)"/></svg></span>
  <p class="copyright">© Copyright 2023 Qvx Brightforge | All Rights Reserved.</p>
</footer>

</body>
</html>
```